VFX Company Business Card Design Project

The Kestrel Works is a decentralized Visual Effects Studio servicing the television and feature film industries.
Project Brief:
Take our logo that was previously designed on Pencil Harbor and make a double sided business card.
Requirements:
- Card MUST be double sided.
- Front of card MUST have the yellow part of our logo against the dark grey background.
- Back of card is completely up to the designer.
- Back of card must include the complete company logo.
Please follow these File Preparation guidelines:
http://printnook.ca/infopage?file=filetype_en&s=PrintNook_new&lang=en
Business

```html
<!DOCTYPE html>
<html lang="en">
<head>
<meta charset="utf-8">
<title>The Kestrel Works – Business Card</title>
<link rel="stylesheet" href="https://fonts.googleapis.com/css2?family=Orbitron:wght@400&family=Roboto:wght@500&display=swap">
<style>
  :root {
    --sky-top: #22f2f6;
    --sky-bottom: #ffffff;
    --card-dark: #1e2423;
    --card-stripe: rgba(255, 255, 255, 0.035);
    --brand-yellow: #f8c31b;
    --ink-light: #f4f6f4;
    --ink-soft: #c9cdcb;
  }
  * { margin: 0; padding: 0; box-sizing: border-box; }
  html, body { width: 1200px; height: 1050px; overflow: hidden; }
  body {
    position: relative;
    background: linear-gradient(180deg, var(--sky-top) 0%, var(--sky-bottom) 100%);
    font-family: "Roboto", Arial, sans-serif;
  }
  .card {
    position: absolute;
    border-radius: 6px;
    background-color: var(--card-dark);
    background-image: repeating-linear-gradient(90deg, var(--card-stripe) 0 1px, transparent 1px 4px);
    box-shadow: 0 1px 3px rgba(0, 0, 0, 0.35);
    overflow: hidden;
  }
  .card--front { left: 86px; top: 35px; width: 748px; height: 509px; }
  .card--back  { left: 446px; top: 566px; width: 661px; height: 444px; }

  .brand-name {
    position: absolute;
    color: var(--brand-yellow);
    font-family: "Roboto", Arial, sans-serif;
    font-weight: 500;
    white-space: nowrap;
  }
  .card--front .brand-name { left: 39px; top: 120px; font-size: 29px; }
  .card--back .brand-name {
    left: 0; right: 0; top: 172px;
    text-align: center; font-size: 58px;
  }

  .holder { position: absolute; right: 44px; top: 176px; text-align: right; }
  .holder__name {
    color: var(--ink-light);
    font-size: 41px;
    font-weight: 500;
    font-variant: small-caps;
    letter-spacing: 1px;
    line-height: 1;
  }
  .holder__rule {
    width: 350px; height: 2px; margin: 6px 0 3px auto;
    background: linear-gradient(90deg, transparent, rgba(255,255,255,0.6) 60%, rgba(255,255,255,0.2));
  }
  .holder__role {
    color: var(--ink-light);
    font-size: 21px;
    font-weight: 500;
    font-variant: small-caps;
    line-height: 1;
  }

  .contact {
    position: absolute; left: 410px; top: 334px;
    width: 300px;
    list-style: none;
    font-family: "Orbitron", "Courier New", sans-serif;
    font-size: 20px;
    letter-spacing: 3.5px;
    color: var(--ink-soft);
    white-space: nowrap;
  }
  .contact li { height: 45px; line-height: 34px; }
</style>
</head>
<body>
  <section class="card card--front" aria-label="Card front">
    <div class="brand-name">The Kestrel Works</div>
    <div class="holder">
      <div class="holder__name">Your Name Here</div>
      <div class="holder__rule"></div>
      <div class="holder__role">Position</div>
    </div>
    <ul class="contact">
      <li>Address here</li>
      <li>mail@kestrel.com</li>
      <li>www.kestrel.com.au</li>
    </ul>
  </section>

  <section class="card card--back" aria-label="Card back">
    <div class="brand-name">The Kestrel Works</div>
  </section>
</body>
</html>
```